web Design for Architecture and Interior Design Firm

This is a complete redesign of an architecture and interior design firm.( http://www.qlbrankworks.com )
We have established a new look-n-feel for them and need to apply it to the new site/new architecture. Wireframes attached with logo and PDF of new brochure.
This will require a quck turn-around. The client is expecting a very modern design with web 2.0 in mind.
Again very quick turn-around! If you cannot commit to a Friday deliverable, do not bid! Must be completed by no later than Friday!

```html
<!DOCTYPE html>
<html lang="en">
<head>
<meta charset="utf-8">
<title>Quinlan Brank Design Studios</title>
<link rel="stylesheet" href="https://fonts.googleapis.com/css2?family=Questrial&family=Arimo:wght@400;700&display=swap">
<style>
  :root {
    --brown: #5e5545;
    --brown-dark: #3a342b;
    --red: #c8102e;
    --red-text: #b5121b;
    --white: #ffffff;
    --ink: #333333;
    --rule: #8a8a8a;
    --field-border: #8d8d8d;
  }
  * { box-sizing: border-box; margin: 0; padding: 0; }
  html, body { width: 1200px; height: 1071px; overflow: hidden; }
  body {
    position: relative;
    font-family: "Arimo", Arial, sans-serif;
    color: var(--ink);
    background: var(--red);
  }
  .backdrop-top {
    position: absolute; left: 0; top: 0; width: 1200px; height: 564px;
    background: linear-gradient(to bottom, var(--brown) 0, var(--brown) 150px, #1a1713 420px, #000 564px);
  }
  .caption-band {
    position: absolute; left: 0; top: 564px; width: 1200px; height: 42px;
    background: var(--brown);
  }
  .page {
    position: absolute; left: 159px; top: 0; width: 882px; height: 1071px;
  }
  .site-header {
    position: absolute; left: 0; top: 0; width: 882px; height: 117px; background: var(--white);
  }
  .brand {
    position: absolute; left: 61px; top: 52px;
    display: flex; align-items: center; gap: 10px; white-space: nowrap;
  }
  .brand-name {
    font-family: "Questrial", sans-serif; font-size: 28px; line-height: 1;
    color: var(--brown);
  }
  .brand-mark { width: 12px; height: 12px; background: var(--red); }
  .main-nav {
    position: absolute; left: 406px; top: 71px;
    display: flex; white-space: nowrap;
    font-family: "Questrial", sans-serif; font-size: 11.5px; letter-spacing: -0.2px;
    text-transform: uppercase; color: var(--brown-dark);
  }
  .main-nav a { color: inherit; text-decoration: none; }
  .main-nav a.is-current { color: var(--red-text); }
  .main-nav .sep { margin: 0 9px; color: #777; }
  .hero {
    position: absolute; left: 0; top: 117px; width: 882px; height: 447px;
    background: radial-gradient(ellipse at 60% 45%, #d9762e 0, #8a4a22 30%, #2b2622 65%, #17140f 100%);
  }
  .hero-caption {
    position: absolute; left: 681px; top: 567px; height: 34px;
    border-left: 2px solid var(--white); padding-left: 10px;
    font-family: "Questrial", sans-serif; font-size: 17px; line-height: 36px; color: var(--white);
  }
  .content {
    position: absolute; left: 0; top: 606px; width: 882px; height: 465px; background: var(--white);
  }
  .intro { position: absolute; left: 43px; top: 24px; width: 518px; }
  .intro h1 {
    width: 440px;
    font-family: "Arimo", Arial, sans-serif; font-weight: 400; font-size: 21px;
    line-height: 27px; color: var(--brown); margin-bottom: 14px;
  }
  .intro p { font-size: 10.3px; line-height: 17px; color: var(--ink); margin-bottom: 17px; }
  .sidebar { position: absolute; left: 613px; top: 28px; width: 225px; }
  .sidebar h2 {
    font-family: "Questrial", sans-serif; font-weight: 400; font-size: 14px;
    text-transform: uppercase; color: var(--brown-dark);
  }
  .news-list { margin-top: 15px; }
  .news-item { font-size: 10px; line-height: 12.5px; margin-bottom: 12px; color: var(--ink); width: 225px; }
  .news-item h3 { font-size: 10px; font-weight: 400; color: var(--red-text); }
  .news-item a { color: var(--ink); }
  .newsletter { margin-top: 32px; }
  .field { display: flex; align-items: center; margin-top: 14px; font-size: 10.3px; }
  .field:first-of-type { margin-top: 20px; }
  .field label { width: 41px; }
  .field input { width: 154px; height: 18px; border: 1px solid var(--field-border); background: var(--white); }
  .field + .field { margin-top: 18px; }
  .actions { display: flex; gap: 10px; margin: 12px 0 0 40px; }
  .btn {
    width: 73px; height: 24px; border: 1px solid #9a9a9a; border-radius: 5px;
    background: linear-gradient(#f2f2f2, #c9c9c9); font-family: "Arimo", Arial, sans-serif;
    font-size: 10px; color: #222;
  }
  .site-footer {
    position: absolute; left: 28px; top: 362px; width: 828px;
    border-top: 1px solid var(--rule); padding-top: 14px;
    display: flex; justify-content: space-between; font-size: 10.3px; color: var(--ink);
  }
  .follow { display: flex; align-items: center; gap: 6px; }
  .social-box { width: 10px; height: 10px; background: #333; display: inline-block; }
</style>
</head>
<body>
  <div class="backdrop-top"></div>
  <div class="caption-band"></div>

  <div class="page">
    <header class="site-header">
      <div class="brand">
        <span class="brand-name">Quinlan Brank</span><span class="brand-mark"></span>
      </div>
      <nav class="main-nav">
        <a class="is-current" href="#">Home</a><span class="sep">|</span>
        <a href="#">About Us</a><span class="sep">|</span>
        <a href="#">Services</a><span class="sep">|</span>
        <a href="#">Portfolio</a><span class="sep">|</span>
        <a href="#">Career</a><span class="sep">|</span>
        <a href="#">Contact Us</a>
      </nav>
    </header>

    <div class="hero" role="img" aria-label="Photo of a meeting room with orange chairs around a white table and a wall of coloured circles"></div>
    <div class="hero-caption">Harlow Media Office</div>

    <main class="content">
      <section class="intro">
        <h1>Quinlan Brank Design Studios Makes the Process Predictable</h1>
        <p>When something as important as the very space in which your business lives and works is about to be disrupted, you should be confident you've chosen the right space and the best team to ensure a successful project. Rely on Quinlan-Brank Design Studios to meet your needs and to make the process predictable. You can be assured that your project goals and objectives will be achieved.</p>
        <p>Rely on Quinlan-Brank Design Studios to meet your needs and to make the process predictable. You can be assured that your project goals and objectives will be achieved. When something as important as the very space in which your business lives and works is about to be disrupted, you should be confident you've chosen the right space and the best team to ensure a successful project.</p>
      </section>

      <aside class="sidebar">
        <h2>News</h2>
        <div class="news-list">
          <article class="news-item">
            <h3>News Title 1</h3>
            Lorem ipsum dolor sit amet, consectetur adipiscing elit. Mauris vitae dui nunc. Nullam lacus lacus...<a href="#">more</a>
          </article>
          <article class="news-item">
            <h3>New Office Location</h3>
            Lorem ipsum dolor sit amet, consectetur adipiscing elit. Mauris vitae dui nunc. Nullam lacus lacus...<a href="#">more</a>
          </article>
        </div>
        <form class="newsletter">
          <h2>Newsletter</h2>
          <div class="field"><label for="nl-name">Name</label><input id="nl-name" type="text"></div>
          <div class="field"><label for="nl-email">Email</label><input id="nl-email" type="email"></div>
          <div class="actions">
            <button class="btn" type="button">Subscribe</button>
            <button class="btn" type="button">Unsubscribe</button>
          </div>
        </form>
      </aside>

      <footer class="site-footer">
        <span>© 2011 Quinlan Brank Design Studios.</span>
        <span class="follow">Follow us&nbsp;<span class="social-box"></span><span class="social-box"></span></span>
      </footer>
    </main>
  </div>
</body>
</html>
```